Health and wellnes company needs business cards

We are a Health and wellness business just relocated to Spain. Here nobody knows our business so we would like to put some of our services on the card. Clean design with logo.

Contact Information for Business Card

Brightmeadow
Paula & Oskar Dunbeck
Calle del Almendro 57
Villacosta del Mar
Mobile: 0046 731 402687
info@brightmeadow.example

Font styles to use
Serif

Colors
85cae6
85acd3
b768aa

Requirements
Must have
• these Services somewhere on the card
• - Private or group yoga
• - Reconnective healing
• - Kitesurfing lessons
• - Massage
• LOgo somewhere
Nice to have
• Colours that go with the logo please

```html
<!DOCTYPE html>
<html lang="en">
<head>
<meta charset="utf-8">
<title>Brightmeadow – Business Card</title>
<link rel="stylesheet" href="https://fonts.googleapis.com/css2?family=Marcellus&family=Varela+Round&display=swap">
<style>
  :root {
    --navy: #1d3a64;
    --navy-top: #264a72;
    --navy-bottom: #1a3660;
    --teal: #6fc5c8;
    --ink: #4a4a4a;
    --rule: #8a8a8a;
    --paper: #ffffff;
    --backdrop: #e4e4e4;
  }
  * { margin: 0; padding: 0; box-sizing: border-box; }
  html, body {
    width: 1200px; height: 1168px; overflow: hidden;
    background: var(--backdrop);
  }
  .card {
    position: absolute; left: 255px; width: 667px; height: 381px;
    border-radius: 22px; overflow: hidden;
    box-shadow: 0 10px 18px rgba(0,0,0,0.22);
  }
  .card-front { top: 161px; background: var(--paper); }
  .card-back {
    top: 636px;
    background: linear-gradient(180deg, var(--navy-top), var(--navy-bottom));
  }

  .brand {
    position: absolute; right: 39px; top: 40px;
    display: flex; flex-direction: column; align-items: center; gap: 12px;
  }
  .brand-dot {
    width: 56px; height: 56px; border-radius: 50%;
    border: 4px solid var(--teal);
  }
  .brand-name {
    font-family: "Marcellus", serif; font-size: 28px;
    color: var(--navy); letter-spacing: 0.5px; line-height: 1;
  }

  .owners {
    position: absolute; left: 33px; top: 230px;
    font-family: "Marcellus", serif; font-size: 16.5px; letter-spacing: 0.3px;
    text-transform: uppercase; color: var(--navy);
  }
  .owners .second { color: var(--teal); }
  .divider {
    position: absolute; left: 33px; right: 39px; top: 261px;
    border-top: 1px solid var(--rule);
  }

  .contact {
    position: absolute; left: 33px; top: 272px;
    font-family: "Varela Round", sans-serif; font-size: 15.5px; color: var(--ink);
    line-height: 20px;
  }
  .contact-row { display: flex; align-items: center; gap: 9px; }
  .contact-row svg { width: 12px; height: 14px; flex: none; }
  .address {
    position: absolute; right: 39px; top: 272px; text-align: right;
    font-family: "Varela Round", sans-serif; font-size: 15.5px; color: var(--ink);
    line-height: 19px;
  }

  .web-band {
    position: absolute; left: 0; right: 0; top: 334px; height: 28px;
    background: linear-gradient(90deg, var(--navy) 0 79.5%, var(--teal) 79.5% 100%);
  }
  .web-address {
    position: absolute; left: 110px; top: 6px;
    font-family: "Varela Round", sans-serif; font-size: 13px;
    letter-spacing: 6.2px; color: var(--paper);
  }
  .band-dot {
    position: absolute; left: 528px; top: 1px; width: 26px; height: 26px;
    border-radius: 50%; background: var(--paper); border: 2px solid var(--navy);
  }

  .back-brand {
    position: absolute; left: 0; right: 0; top: 88px;
    display: flex; flex-direction: column; align-items: center; gap: 18px;
  }
  .back-dot {
    width: 120px; height: 120px; border-radius: 50%;
    border: 10px solid var(--paper);
  }
  .back-name {
    font-family: "Marcellus", serif; font-size: 30px;
    color: var(--paper); letter-spacing: 1px; line-height: 1;
  }
  .services {
    position: absolute; left: 39px; right: 39px; top: 315px;
    display: flex; justify-content: space-between;
    font-family: "Varela Round", sans-serif; font-size: 15.5px;
    color: var(--paper); list-style: none; white-space: nowrap;
  }
  .services li + li::before { content: "•"; margin-right: 6px; font-size: 12px; }
</style>
</head>
<body>
  <section class="card card-front">
    <div class="brand">
      <span class="brand-dot"></span>
      <span class="brand-name">BRIGHTMEADOW</span>
    </div>

    <p class="owners">Paula &amp; <span class="second">Oskar Dunbeck</span></p>
    <div class="divider"></div>

    <div class="contact">
      <p class="contact-row">
        <svg viewBox="0 0 12 14" aria-hidden="true"><rect x="1.5" y="0.8" width="9" height="12.4" rx="1.5" fill="none" stroke="#1d3a64" stroke-width="1.6"/><rect x="4.5" y="10.3" width="3" height="1.2" fill="#1d3a64"/></svg>
        0046 731 402687
      </p>
      <p class="contact-row">
        <svg viewBox="0 0 12 14" aria-hidden="true"><rect x="0.5" y="3.5" width="11" height="8" fill="#1d3a64"/><path d="M0.8 3.8 L6 8 L11.2 3.8" fill="none" stroke="#fff" stroke-width="1"/></svg>
        info@brightmeadow.example
      </p>
    </div>

    <div class="address">
      <p>Calle del Almendro 57</p>
      <p>Villacosta del Mar</p>
    </div>

    <div class="web-band">
      <span class="web-address">www.brightmeadow.example</span>
      <span class="band-dot"></span>
    </div>
  </section>

  <section class="card card-back">
    <div class="back-brand">
      <span class="back-dot"></span>
      <span class="back-name">BRIGHTMEADOW</span>
    </div>
    <ul class="services">
      <li>Private or group yoga</li>
      <li>Reconnective healing</li>
      <li>Kitesurfing lessons</li>
      <li>Massage</li>
    </ul>
  </section>
</body>
</html>
```